Valdo Capital

We need a corporate style website design for a new company based in Shenzhen's Qianhai Special Economic Development Zone, China. We provide a range of financial services to large international investment companies. Typically these companies invest over 5 million RMB. The company is part of a group that consists of NorthKilns, ValdoTrusts and ValdoEquity. Our location and gateway into Qianhai Special Economic Zone is our core advantage. We would like to see designs that Do Not use purple and orange. The website design should be similar to other websites in this family but different enough to give it a unique style (See attached website links for reference). The final design should communicate financial safety and growth. This website will act partly as a business chamber with connections to the government so we would like it to be diplomatic in style.

www.northkilns.example
www.valdotrusts.example

*Nevegation Bar
Should including Homepage, Financial Product, Team, News.
Could refer to www.valdotrusts.example

*Contact Details

Miss Lan
Address:E 728, North Block, KMO Centre, East Sector, Shenzhen Bright Science Campus
Telephone: +86 0755 63920417
Cellphone: +86 13957280316

* Social Media
Should be grouped like:
1. Weibo QRcode+ Weibo
2. Facebook, Twitter, Linkedin.

Industry/Entity Type

Investment

```html
<!DOCTYPE html>
<html lang="en">
<head>
<meta charset="utf-8">
<title>Valdo Capital</title>
<link rel="stylesheet" href="https://fonts.googleapis.com/css2?family=Open+Sans:wght@300;400;600;700&display=swap">
<style>
:root{
  --bar:#1c1c1c;
  --bar-line:#3a3a3a;
  --text-light:#d8d8d8;
  --text-muted:#8d8d8d;
  --accent:#4aa3d6;
  --ink:#222222;
  --body:#3c3c3c;
  --white:#ffffff;
  --icon:#6d6d6d;
}
*{margin:0;padding:0;box-sizing:border-box}
html,body{width:1200px;height:986px;overflow:hidden;background:var(--bar)}
body{font-family:"Open Sans",Arial,sans-serif;position:relative}
.site-header{position:absolute;left:0;top:0;width:1200px;height:107px;background:var(--bar);z-index:3}
.brand{position:absolute;left:110px;top:0;width:341px;height:119px;background:var(--white);display:flex;align-items:center;padding-left:24px;gap:16px;z-index:4}
.brand-mark{width:22px;height:22px;background:var(--ink)}
.brand-name{font-size:27px;font-weight:600;color:var(--ink);letter-spacing:1px}
.utility{position:absolute;top:17px;right:110px;display:flex;align-items:center;height:22px;color:var(--text-light);font-size:13px}
.lang{margin-right:18px}
.lang b{font-weight:600;text-decoration:underline;color:var(--text-light)}
.lang .sep{margin:0 5px}
.lang .caret{display:inline-block;margin-left:8px;border:4px solid transparent;border-top:5px solid var(--text-light);border-bottom:0;vertical-align:middle}
.phone{display:flex;align-items:center;gap:8px;font-size:15px;margin-right:16px}
.social{display:flex;gap:6px}
.social span{width:26px;height:26px;border-radius:50%;background:var(--icon);display:block}
.header-rule{position:absolute;left:481px;top:55px;width:609px;height:1px;background:var(--bar-line)}
.main-nav{position:absolute;right:110px;top:70px;display:flex;align-items:center;font-size:13px;color:var(--text-light)}
.main-nav a{color:inherit;text-decoration:none;margin-left:30px}
.main-nav a.active{color:var(--accent)}
.main-nav .divider{width:1px;height:20px;background:var(--bar-line);margin:0 10px 0 14px}
.hero{position:absolute;left:0;top:107px;width:1200px;height:824px;
  background:
    linear-gradient(180deg,rgba(0,0,0,0) 70%,rgba(0,0,0,.85) 100%),
    linear-gradient(90deg,rgba(120,80,20,.55) 0%,rgba(60,40,20,.2) 40%,rgba(0,0,0,0) 60%),
    linear-gradient(180deg,#3a4f70 0%,#2a4a7a 30%,#2f5d8f 55%,#4a5560 68%,#2a2a30 82%,#0c0c0c 100%)}
.hero-copy{position:absolute;left:633px;top:173px;width:460px;color:var(--white)}
.hero-copy h1{font-weight:300;font-size:60px;line-height:60px;letter-spacing:-1px}
.hero-copy h1 strong{display:block;font-weight:600;font-size:62px;line-height:62px}
.hero-copy p{margin-top:8px;margin-left:4px;font-size:17px;line-height:22.5px}
.read-more{display:inline-block;margin-top:18px;margin-left:4px;font-size:17px;color:var(--white);text-decoration:underline}
.read-more::after{content:"";display:inline-block;margin-left:6px;border:4px solid transparent;border-left:5px solid #ccc;border-right:0}
.features{position:absolute;left:110px;top:733px;width:980px;height:198px;background:var(--white);display:flex;z-index:2}
.feature{flex:1;padding:12px 14px 0;border-left:1px solid #d5d5d5}
.feature:first-child{border-left:0}
.feature h2{font-size:19px;font-weight:600;color:var(--ink);line-height:22px}
.feature h2 strong{display:block;font-size:34px;font-weight:700;line-height:34px;letter-spacing:-.5px}
.feature p{margin-top:9px;font-size:13px;line-height:20px;color:var(--body)}
.btn{display:inline-block;margin-top:17px;height:26px;line-height:26px;padding:0 18px;background:var(--ink);color:var(--white);font-size:12px;font-weight:600;text-decoration:none;clip-path:polygon(10px 0,calc(100% - 10px) 0,100% 50%,calc(100% - 10px) 100%,10px 100%,0 50%)}
.site-footer{position:absolute;left:0;top:931px;width:1200px;height:55px;background:var(--bar)}
.footer-nav{position:absolute;left:111px;top:20px;font-size:12px;color:var(--text-muted)}
.footer-nav a{color:inherit;text-decoration:none}
.footer-nav .dot{margin:0 13px}
.copyright{position:absolute;right:110px;top:11px;font-size:12px;line-height:18px;color:var(--text-muted);text-align:right}
</style>
</head>
<body>
<header class="site-header">
  <div class="brand"><span class="brand-mark"></span><span class="brand-name">VALDO CAPITAL</span></div>
  <div class="utility">
    <div class="lang"><b>EN</b><span class="sep">|</span>SP<span class="caret"></span></div>
    <div class="phone">
      <svg width="8" height="14" viewBox="0 0 8 14"><rect x="0.5" y="0.5" width="7" height="13" rx="1.2" fill="none" stroke="#d8d8d8"/><rect x="3" y="11" width="2" height="1" fill="#d8d8d8"/></svg>
      +86 0755 63920417
    </div>
    <div class="social" aria-label="Social links"><span></span><span></span><span></span></div>
  </div>
  <div class="header-rule"></div>
  <nav class="main-nav">
    <a class="active" href="#">HOME</a>
    <a href="#">FINANCIAL PRODUCTS</a>
    <a href="#">TEAM</a>
    <a href="#">NEWS</a>
    <span class="divider"></span>
    <svg width="19" height="19" viewBox="0 0 19 19" aria-label="Search"><circle cx="7.5" cy="7.5" r="5.8" fill="none" stroke="#8d8d8d" stroke-width="2.4"/><line x1="11.8" y1="11.8" x2="17.5" y2="17.5" stroke="#8d8d8d" stroke-width="3" stroke-linecap="round"/></svg>
  </nav>
</header>

<section class="hero" role="img" aria-label="Night skyline of a harbour city with lit towers and waterfront">
  <div class="hero-copy">
    <h1>Welcome To<strong>Valdo Capital</strong></h1>
    <p>Lorem ipsum dolor sit amet, consectetur adipisicing elit, sed do eiusmod tempor incididunt ut labore et dolore magna aliqua..</p>
    <a class="read-more" href="#">Read More</a>
  </div>
</section>

<section class="features">
  <article class="feature">
    <h2>VALDO CAPITAL<strong>SERVICES</strong></h2>
    <p>Lorem ipsum dolor sit amet, consectetur adipisicing elit, sed do eiusmod tempor incididunt ut labore et dolore magna aliqua.</p>
    <a class="btn" href="#">VIEW ALL SERVICES</a>
  </article>
  <article class="feature">
    <h2>VALDO CAPITAL<strong>BLOG</strong></h2>
    <p>Lorem ipsum dolor sit amet, consectetur adipisicing elit, sed do eiusmod tempor incididunt ut labore et dolore magna aliqua.</p>
    <a class="btn" href="#">VIEW ALL SERVICES</a>
  </article>
  <article class="feature">
    <h2>VALDO CAPITAL<strong>NEWS</strong></h2>
    <p>Lorem ipsum dolor sit amet, consectetur adipisicing elit, sed do eiusmod tempor incididunt ut labore et dolore magna aliqua.</p>
    <a class="btn" href="#">VIEW ALL SERVICES</a>
  </article>
</section>

<footer class="site-footer">
  <nav class="footer-nav">
    <a href="#">HOME</a><span class="dot">•</span><a href="#">FINANCIAL PRODUCTS</a><span class="dot">•</span><a href="#">TEAM</a><span class="dot">•</span><a href="#">NEWS</a>
  </nav>
  <div class="copyright">COPYRIGHT © 2014 VALDOCAPITAL.EXAMPLE<br>ALL RIGHTS RESERVED.</div>
</footer>
</body>
</html>
```